Coastal Learner Bureau business cards

Australian company about to start offering its services. We recruit international students to come to study English, vocational education and postgraduate courses in Australia. We help them find the institution and select the right city they want to come to Australia. We are a young, online oriented and supportive agency. Our clients are between 18 and 35 years old, mainly University students, young professionals or people with work experience. We provide much more information that any other agency offer. We administrate a Facebook group with more than 11.000 members that daily ask questions about general information when coming to Australia, while they are here and even after they leave the country

Target Market(s)

International students from South America, Central America and Europe

Industry/Entity Type

Student

Contact Information for Business Card

Tomas Bilbrea
Managing Director
tomas@kelvarin.com.au
www.kelvoria.com.au
+61 491058264
Carrowdale, Victoria

Font styles to use
Serif
Sans Serif

Colors

Designer to choose colors to be used in the design.

Requirements
Must have
• Horizontal design
• Standard business card size and shape. If font uses green or yellow colours, they will have to match the ones from the logo
Nice to have
• UPDATE: Use the contents of the green image to design one of the card sides. Use our logo in the background of that side as watermark.
• Passport image, or immigration stamps. A picture of the Yarra River (from Melbourne) would be cool as well.
Should not have
• Non-standard business card size and shape
• Not black as the background colour of any sides as we are not a VIP agency or a hight class service. We are orientes to young people and they like colours, pictures, something attractive.
• Vertical design
• NO YELLOW or BLACK AS THE BACKGROUND COLOUR OF ANY SIDE OF THE BIZ CARD

```html
<!DOCTYPE html>
<html lang="en">
<head>
<meta charset="utf-8">
<title>Coastal Learner Bureau — Business Cards</title>
<link rel="stylesheet" href="https://fonts.googleapis.com/css2?family=Oswald:wght@600&family=Jost:wght@400;500&display=swap">
<style>
  :root {
    --backdrop: #cbcbcb;
    --card-white: #ffffff;
    --brand-green: #0e6342;
    --brand-yellow: #e3b521;
    --ink: #3a3a3a;
  }
  * { margin: 0; padding: 0; box-sizing: border-box; }
  html, body {
    width: 1200px; height: 1000px; overflow: hidden;
    background: var(--backdrop);
  }
  .canvas { position: relative; width: 1200px; height: 1000px; }

  .card {
    position: absolute; left: 295px; width: 587px; height: 335px;
  }
  .card-front { top: 149px; background: var(--card-white); }
  .card-back { top: 517px; background: var(--brand-green); }

  .identity {
    position: absolute; right: 320px; top: 152px; text-align: right;
  }
  .person-name {
    font-family: "Oswald", sans-serif; font-weight: 600;
    font-size: 24px; letter-spacing: 0.2px; line-height: 1;
    color: var(--brand-green);
  }
  .person-role {
    margin-top: 11px;
    font-family: "Jost", sans-serif; font-size: 17.5px; line-height: 1;
    color: var(--ink);
  }
  .divider {
    position: absolute; left: 286px; top: 148px;
    width: 2px; height: 67px; background: var(--brand-green);
  }
  .contact-list {
    position: absolute; left: 305px; top: 143px; list-style: none;
  }
  .contact-item {
    display: flex; align-items: center; height: 18.7px;
    font-family: "Jost", sans-serif; font-size: 14px;
    letter-spacing: 0.6px; color: var(--ink);
  }
  .contact-icon { width: 10px; height: 10px; margin-right: 12px; flex: none; }
  .contact-icon path, .contact-icon circle, .contact-icon rect { fill: var(--brand-green); }
  .contact-icon .stroke { fill: none; stroke: var(--brand-green); stroke-width: 2; }

  .accent-band {
    position: absolute; left: 0; bottom: 0; width: 100%; height: 18px; display: flex;
  }
  .accent-green { flex: 1; background: var(--brand-green); }
  .accent-yellow { flex: 1; background: var(--brand-yellow); }

  .brand-lockup {
    position: absolute; left: 0; right: 0; top: 140px;
    display: flex; justify-content: center; align-items: center; gap: 12px;
  }
  .brand-dot {
    width: 14px; height: 14px; border-radius: 50%; background: var(--card-white);
  }
  .brand-name {
    font-family: "Jost", sans-serif; font-weight: 500;
    font-size: 46px; line-height: 1; color: var(--card-white);
  }
  .tagline {
    position: absolute; left: 0; right: 0; top: 288px; text-align: center;
    font-family: "Jost", sans-serif; font-weight: 500;
    font-size: 14px; letter-spacing: 0.5px; color: var(--card-white);
  }
</style>
</head>
<body>
<main class="canvas">
  <section class="card card-front" aria-label="Card front">
    <div class="identity">
      <p class="person-name">TOMAS BILBREA</p>
      <p class="person-role">Managing Director</p>
    </div>
    <div class="divider"></div>
    <ul class="contact-list">
      <li class="contact-item">
        <svg class="contact-icon" viewBox="0 0 10 10" aria-hidden="true"><rect class="stroke" x="2.5" y="1" width="5" height="8" rx="0.8"/></svg>
        +61 491058264
      </li>
      <li class="contact-item">
        <svg class="contact-icon" viewBox="0 0 10 10" aria-hidden="true"><path d="M0 2h10v6H0z"/><path d="M0 2l5 3.5L10 2" fill="none" stroke="#fff" stroke-width="1"/></svg>
        tomas@kelvarin.com.au
      </li>
      <li class="contact-item">
        <svg class="contact-icon" viewBox="0 0 10 10" aria-hidden="true"><circle class="stroke" cx="4" cy="4" r="2.8"/><path d="M5.8 6.3l1.3-1.3 2.9 2.9-1.3 1.3z"/></svg>
        www.kelvoria.com.au
      </li>
      <li class="contact-item">
        <svg class="contact-icon" viewBox="0 0 10 10" aria-hidden="true"><path d="M5 0a3.6 3.6 0 0 1 3.6 3.6C8.6 6.3 5 10 5 10S1.4 6.3 1.4 3.6A3.6 3.6 0 0 1 5 0zm0 2.2a1.4 1.4 0 1 0 0 2.8 1.4 1.4 0 0 0 0-2.8z"/></svg>
        Carrowdale, Victoria
      </li>
    </ul>
    <div class="accent-band">
      <span class="accent-green"></span>
      <span class="accent-yellow"></span>
    </div>
  </section>

  <section class="card card-back" aria-label="Card back">
    <div class="brand-lockup">
      <span class="brand-dot"></span>
      <span class="brand-name">Kelvoria</span>
    </div>
    <p class="tagline">Vamos contigo siempre!</p>
  </section>
</main>
</body>
</html>
```